The most modern business card ever !!!

Our company call “Vendalo”. Vendalo is a technology company specialized in cruises solutions. Out main product is a platform to reserve cruises. This is a revolutionary platform that make easier to travel agencies and final users to reserve cruises across dozen companies like tibba, wernu, hpv, dgb, etc..We are a “start up”, with a young team of developers and we want to transmit it.. For it, we want something different, a modern business card that represent cruises and technology.. When someone receive this card, this person should say: wowww this is different… this is modern… this is a cruise related company..
- diferent, modern
- traditions business card

```html
<!DOCTYPE html>
<html lang="pt">
<head>
<meta charset="utf-8">
<title>Vendalo – Business Card</title>
<link rel="stylesheet" href="https://fonts.googleapis.com/css2?family=Exo+2:wght@400;600;700&display=swap">
<style>
  :root {
    --bg: #e9e7e3;
    --card-white: #ffffff;
    --card-black: #070909;
    --accent-blue: #23a0d6;
    --ink: #1b1b1d;
    --muted-mark: #1a1d1f;
  }
  * { margin: 0; padding: 0; box-sizing: border-box; }
  html, body { width: 1200px; height: 1021px; overflow: hidden; }
  body {
    background: var(--bg);
    font-family: "Exo 2", sans-serif;
    color: var(--ink);
    position: relative;
  }
  .card {
    position: absolute;
    left: 190px;
    width: 820px;
    height: 450px;
  }
  .card--front { top: 45px; }
  .card--back { top: 526px; }
  .card-shape { position: absolute; inset: 0; width: 820px; height: 450px; filter: drop-shadow(0 4px 10px rgba(0,0,0,.18)); }

  .brand-name {
    position: absolute;
    left: 62px; top: 48px;
    font-size: 74px;
    font-weight: 600;
    letter-spacing: 1px;
    color: var(--ink);
    line-height: 1;
  }
  .person { position: absolute; left: 66px; top: 150px; }
  .person-name { font-size: 30px; font-weight: 700; color: var(--accent-blue); line-height: 1.1; }
  .person-role { font-size: 21px; font-weight: 400; line-height: 1.2; }

  .company { position: absolute; left: 66px; top: 232px; font-size: 19px; line-height: 1.3; }
  .company-name { font-weight: 700; }

  .contacts { position: absolute; left: 66px; top: 326px; list-style: none; font-size: 19px; line-height: 1.4; }
  .contacts li { display: flex; align-items: center; gap: 8px; }
  .contacts svg { width: 16px; height: 16px; flex: none; }

  .back-mark {
    position: absolute;
    left: 290px; top: 180px;
    font-size: 86px;
    font-weight: 600;
    letter-spacing: 2px;
    color: var(--muted-mark);
    line-height: 1;
  }
</style>
</head>
<body>

<section class="card card--front" aria-label="Card front">
  <svg class="card-shape" viewBox="0 0 820 450" aria-hidden="true">
    <defs>
      <clipPath id="front-outline"><polygon points="0,0 640,0 820,225 640,450 0,450"/></clipPath>
    </defs>
    <polygon points="0,0 640,0 820,225 640,450 0,450" fill="var(--card-white)"/>
    <g clip-path="url(#front-outline)">
      <polyline points="575,-20 771,225 575,470" fill="none" stroke="var(--accent-blue)" stroke-width="30"/>
    </g>
  </svg>

  <div class="brand-name">Vendalo</div>

  <div class="person">
    <div class="person-name">Marcos Elwin</div>
    <div class="person-role">Developer</div>
  </div>

  <div class="company">
    <div class="company-name">Vendalo Tecnologia Em Informatica Eireli</div>
    <div>R Doutor Teles Barra 148, Sala 17</div>
    <div>Vila Nereida, Ponte Alta, SP, 09315-480, Brasil</div>
  </div>

  <ul class="contacts">
    <li>
      <svg viewBox="0 0 16 16" aria-hidden="true"><path fill="var(--accent-blue)" d="M3.6 1.2l2.3 2.6-1.3 1.9c.9 2 2.6 3.7 4.6 4.6l1.9-1.3 2.6 2.3-1.4 2.4C6.9 14.3 1.7 9.1 1.2 3z"/></svg>
      (11) 5550-2817
    </li>
    <li>
      <svg viewBox="0 0 16 16" aria-hidden="true"><rect x="1" y="3" width="14" height="10" fill="none" stroke="var(--accent-blue)" stroke-width="1.6"/><path d="M1 3l7 6 7-6" fill="none" stroke="var(--accent-blue)" stroke-width="1.6"/></svg>
      rafa@vendalo.com.br
    </li>
    <li>
      <svg viewBox="0 0 16 16" aria-hidden="true"><g fill="none" stroke="var(--accent-blue)" stroke-width="1.3"><circle cx="8" cy="8" r="6.5"/><ellipse cx="8" cy="8" rx="3" ry="6.5"/><path d="M1.5 8h13M2.5 4.7h11M2.5 11.3h11"/></g></svg>
      www.vendalo.com.br
    </li>
  </ul>
</section>

<section class="card card--back" aria-label="Card back">
  <svg class="card-shape" viewBox="0 0 820 450" aria-hidden="true">
    <defs>
      <clipPath id="back-outline"><polygon points="180,0 820,0 820,450 180,450 0,225"/></clipPath>
    </defs>
    <polygon points="180,0 820,0 820,450 180,450 0,225" fill="var(--card-black)"/>
    <g clip-path="url(#back-outline)">
      <polyline points="245,-20 49,225 245,470" fill="none" stroke="var(--accent-blue)" stroke-width="30"/>
    </g>
  </svg>
  <div class="back-mark">Vendalo</div>
</section>

</body>
</html>
```